Moravel Aesthetic Doctor

I require an elegant, luxurious looking business card for my aesthetic business. I am a doctor and that will set me aside from competitors. I am planning to provide home and spa based treatments to clients with high expectations. I have attached my logo.

```html
<!DOCTYPE html>
<html lang="en">
<head>
<meta charset="utf-8">
<title>Moravel Aesthetic Doctor — Business Card</title>
<link rel="stylesheet" href="https://fonts.googleapis.com/css2?family=Marcellus&family=Oswald:wght@300&family=Arimo:wght@400;700&display=swap">
<style>
  :root {
    --stage: #232323;
    --card-white: #ffffff;
    --ink-grey: #9a9ca0;
    --ink-dark-grey: #8a8c90;
    --sky: #5bbbe8;
    --icon-blue: #58b8e6;
    --rule: #8d8f92;
    --blue-top: #1d8ce0;
    --blue-bottom: #0a63c2;
    --white: #ffffff;
  }
  * { margin: 0; padding: 0; box-sizing: border-box; }
  html, body { width: 1200px; height: 1108px; overflow: hidden; }
  body {
    background: var(--stage);
    font-family: "Arimo", Arial, sans-serif;
    position: relative;
  }
  .card {
    position: absolute;
    top: 194px;
    width: 440px;
    height: 720px;
    border-radius: 22px;
    overflow: hidden;
  }
  .card--front { left: 130px; background: var(--card-white); }
  .card--back {
    left: 630px;
    background: linear-gradient(160deg, var(--blue-top), var(--blue-bottom));
    color: var(--white);
  }

  /* Front */
  .brand {
    position: absolute;
    top: 150px;
    left: 0; right: 0;
    display: flex;
    flex-direction: column;
    align-items: center;
  }
  .brand__row { display: flex; align-items: center; gap: 16px; }
  .brand__dot {
    width: 56px; height: 56px; border-radius: 50%;
    background: var(--sky);
  }
  .brand__name {
    font-family: "Marcellus", Georgia, serif;
    font-size: 64px;
    letter-spacing: 2px;
    color: var(--ink-grey);
    line-height: 1;
  }
  .brand__tagline {
    font-family: "Oswald", "Arial Narrow", sans-serif;
    font-weight: 300;
    font-size: 26px;
    letter-spacing: 3px;
    color: var(--sky);
    margin-top: 6px;
    margin-left: 60px;
  }
  .person {
    position: absolute;
    top: 360px; left: 0; right: 0;
    text-align: center;
  }
  .person__name {
    font-size: 30px; font-weight: 700; color: var(--ink-grey);
  }
  .person__letters {
    font-size: 17px; font-weight: 400; color: var(--sky); margin-left: 4px;
  }
  .person__credential {
    font-size: 22px; color: var(--sky); line-height: 1.25; margin-top: 6px;
  }
  .divider {
    position: absolute; left: 70px; right: 70px;
    display: flex; align-items: center; gap: 10px;
  }
  .divider::before, .divider::after {
    content: ""; flex: 1; height: 1px; background: var(--rule);
  }
  .divider--icons { top: 482px; }
  .divider--social { top: 636px; }
  .contact-icon {
    width: 38px; height: 38px; border-radius: 6px;
    background: var(--icon-blue);
    display: flex; align-items: center; justify-content: center;
  }
  .social-dot {
    width: 36px; height: 36px; border-radius: 50%;
    background: var(--ink-grey);
  }
  .contact {
    position: absolute; top: 540px; left: 0; right: 0;
    text-align: center; list-style: none;
    font-size: 22px; color: var(--ink-dark-grey); line-height: 1.3;
  }

  /* Back */
  .back__pattern {
    position: absolute; inset: 0;
    background: radial-gradient(circle at 50% 40%, rgba(255,255,255,0.08), rgba(255,255,255,0) 70%);
  }
  .back__mark {
    position: absolute; top: 250px; left: 0; right: 0;
    text-align: center;
    font-family: "Marcellus", Georgia, serif;
    font-size: 40px; letter-spacing: 2px; color: var(--white);
  }
  .services {
    position: absolute; top: 380px; left: 0; right: 0;
    list-style: none; text-align: center;
    font-size: 25px; line-height: 1.42; letter-spacing: 0.5px;
  }
  .back__footer {
    position: absolute; bottom: 60px; left: 0; right: 0;
    text-align: center; font-size: 22px; font-weight: 700; letter-spacing: 0.5px;
  }
</style>
</head>
<body>
  <section class="card card--front">
    <div class="brand">
      <div class="brand__row">
        <span class="brand__dot"></span>
        <span class="brand__name">MORAVEL</span>
      </div>
      <span class="brand__tagline">AESTHETIC DOCTOR</span>
    </div>

    <div class="person">
      <p class="person__name">Dr Elise Varden<span class="person__letters">MRCPCH MD</span></p>
      <p class="person__credential">Australasian Diploma of<br>Aesthetic Medicine</p>
    </div>

    <div class="divider divider--icons">
      <span class="contact-icon" aria-label="Phone">
        <svg width="22" height="22" viewBox="0 0 24 24"><path d="M6.6 10.8a15 15 0 0 0 6.6 6.6l2.2-2.2a1 1 0 0 1 1-.25 11.4 11.4 0 0 0 3.6.57 1 1 0 0 1 1 1V20a1 1 0 0 1-1 1A17 17 0 0 1 3 4a1 1 0 0 1 1-1h3.5a1 1 0 0 1 1 1c0 1.25.2 2.45.57 3.57a1 1 0 0 1-.25 1z" fill="#fff"/></svg>
      </span>
      <span class="contact-icon" aria-label="Email">
        <svg width="22" height="22" viewBox="0 0 24 24"><rect x="3" y="6" width="18" height="12" fill="none" stroke="#fff" stroke-width="1.8"/><path d="M3 6l9 7 9-7" fill="none" stroke="#fff" stroke-width="1.8"/></svg>
      </span>
      <span class="contact-icon" aria-label="Website">
        <svg width="22" height="22" viewBox="0 0 24 24"><circle cx="12" cy="12" r="8.5" fill="none" stroke="#fff" stroke-width="1.8"/><path d="M3.5 12h17M12 3.5c3 3 3 14 0 17M12 3.5c-3 3-3 14 0 17" fill="none" stroke="#fff" stroke-width="1.4"/></svg>
      </span>
    </div>

    <ul class="contact">
      <li>0800 555 014</li>
      <li>elise@moravel.co.nz</li>
      <li>www.moravel.co.nz</li>
    </ul>

    <div class="divider divider--social">
      <span class="social-dot" aria-label="Social profile"></span>
      <span class="social-dot" aria-label="Social profile"></span>
    </div>
  </section>

  <section class="card card--back">
    <div class="back__pattern" role="img" aria-label="Subtle repeating brand emblem pattern on blue"></div>
    <p class="back__mark">MORAVEL</p>
    <ul class="services">
      <li>DERMAL INJECTABLES</li>
      <li>PLASMA FACIALS</li>
      <li>MICRONEEDLING</li>
      <li>SKIN BOOSTERS</li>
      <li>EXCESSIVE SWEATING</li>
    </ul>
    <p class="back__footer">HOME AND SPA BASED TREATMENTS</p>
  </section>
</body>
</html>
```